Dane Warbeck Photography Business Card

I am looking for a simple, yet elegant business card for my photography business.

It is a short turn around project as the cards need to be printed within 48 hours. So the earlier you submit, the more likely you are to be chosen.

I am a professional portrait, sports and commercial photographer located in Brisbane, Australia. I am looking for a professional business card to distribute to professional clients. The card needs to be professional and easy to read. It must have my contact information as listed below.

Industry/Entity Type

Business

Contact Information for Business Card

Dane Warbeck Photography
www.danewarbeckphoto.com.au
dane@danewarbeckphoto.com.au
+61 437 582 906

Font styles to use
Serif
Sans Serif

Colors
ffc214
fece3e
fee18a

Requirements
Must have
• Must have contact information as above,
• Please use a similar colourscheme to the one provided in the logo upload.
Nice to have
• A very simple, design, happy to have some geometric shapes etc. Must look professional

```html
<!DOCTYPE html>
<html lang="en">
<head>
<meta charset="utf-8">
<title>Dane Warbeck Photography – Business Card</title>
<link href="https://fonts.googleapis.com/css2?family=Nunito+Sans:wght@300;400&display=swap" rel="stylesheet">
<style>
  :root {
    --card-bg: #e7e8ea;
    --shard-dark: #3a3a3c;
    --shard-yellow: #ffcd3a;
    --mark-gold: #d8961f;
    --ink: #3f3f42;
  }
  html, body {
    margin: 0;
    padding: 0;
    overflow: hidden;
    background: var(--card-bg);
  }
  .card {
    position: relative;
    width: 1200px;
    height: 686px;
    background: var(--card-bg);
    overflow: hidden;
  }
  .card__shards {
    position: absolute;
    inset: 0;
    width: 1200px;
    height: 686px;
  }
  .shard--dark { fill: var(--shard-dark); }
  .shard--yellow { fill: var(--shard-yellow); }
  .brand-mark { fill: var(--mark-gold); }
  .brand-name {
    position: absolute;
    left: 440px;
    top: 268px;
    margin: 0;
    font-family: "Nunito Sans", sans-serif;
    font-weight: 300;
    color: var(--ink);
    line-height: 1;
    text-transform: uppercase;
    white-space: nowrap;
  }
  .brand-name__primary {
    display: block;
    font-size: 84px;
    letter-spacing: -2px;
  }
  .brand-name__secondary {
    display: block;
    margin-top: 10px;
    margin-left: 4px;
    font-size: 48px;
  }
  .contact {
    position: absolute;
    left: 600px;
    top: 572px;
    transform: translateX(-50%);
    margin: 0;
    font-family: "Nunito Sans", sans-serif;
    font-weight: 400;
    font-style: normal;
    font-size: 20px;
    line-height: 28px;
    color: var(--ink);
    text-align: center;
    white-space: nowrap;
  }
  .contact__line { display: block; }
</style>
</head>
<body>
  <main class="card">
    <svg class="card__shards" viewBox="0 0 1200 686" aria-hidden="true">
      <polygon class="shard--yellow" points="155,0 300,0 1040,232"/>
      <polygon class="shard--dark" points="300,0 680,0 1040,232"/>
      <polygon class="shard--dark" points="0,612 582,455 218,686 0,686"/>
      <polygon class="shard--yellow" points="582,455 218,686 290,686"/>
      <polygon class="shard--yellow" points="790,540 900,686 975,686"/>
      <polygon class="shard--dark" points="790,540 1200,655 1200,686 975,686"/>
      <circle class="brand-mark" cx="280" cy="341" r="115"/>
    </svg>
    <h1 class="brand-name">
      <span class="brand-name__primary">Dane Warbeck</span>
      <span class="brand-name__secondary">Photography</span>
    </h1>
    <address class="contact">
      <span class="contact__line">www.danewarbeckphoto.com.au</span>
      <span class="contact__line">dane@danewarbeckphoto.com.au</span>
      <span class="contact__line">+61 437 582 906</span>
    </address>
  </main>
</body>
</html>
```